Coastal Learner Bureau business cards

Australian company about to start offering its services. We recruit international students to come to study English, vocational education and postgraduate courses in Australia. We help them find the institution and select the right city they want to come to Australia. We are a young, online oriented and supportive agency. Our clients are between 18 and 35 years old, mainly University students, young professionals or people with work experience. We provide much more information that any other agency offer. We administrate a Facebook group with more than 11.000 members that daily ask questions about general information when coming to Australia, while they are here and even after they leave the country

Target Market(s)

International students from South America, Central America and Europe

Industry/Entity Type

Student

Contact Information for Business Card

Tomas Bilbrea
Managing Director
tomas@kelvarin.com.au
www.kelvoria.com.au
+61 491058264
Melbourne, Australia

Font styles to use
Serif
Sans Serif

Colors

Designer to choose colors to be used in the design.

Requirements
Must have
• Horizontal design
• Standard business card size and shape. If font uses green or yellow colours, they will have to match the ones from the logo
Nice to have
• UPDATE: Use the contents of the green image to design one of the card sides. Use our logo in the background of that side as watermark.
• Passport image, or immigration stamps. A picture of the Yarra River (from Melbourne) would be cool as well.
Should not have
• Non-standard business card size and shape
• Not black as the background colour of any sides as we are not a VIP agency or a hight class service. We are orientes to young people and they like colours, pictures, something attractive.
• Vertical design
• NO YELLOW or BLACK AS THE BACKGROUND COLOUR OF ANY SIDE OF THE BIZ CARD

```html
<!DOCTYPE html>
<html lang="en">
<head>
<meta charset="utf-8">
<title>Kelvoria business cards</title>
<link rel="stylesheet" href="https://fonts.googleapis.com/css2?family=Open+Sans:wght@400;600;700&display=swap">
<style>
  :root {
    --page: #e9e7e4;
    --card-top: #0f5a6b;
    --card-bottom: #14786f;
    --green: #8fdc8a;
    --yellow: #f2c544;
    --ink: #f4f7f6;
    --rule: rgba(255,255,255,.7);
  }
  * { box-sizing: border-box; margin: 0; padding: 0; }
  html, body { width: 1200px; height: 864px; overflow: hidden; }
  body {
    background: var(--page);
    font-family: "Open Sans", Arial, sans-serif;
    display: flex;
    align-items: center;
    justify-content: center;
    gap: 36px;
  }
  .card {
    width: 560px;
    height: 320px;
    background: linear-gradient(135deg, var(--card-top), var(--card-bottom));
    border-radius: 4px;
    position: relative;
    box-shadow: 0 10px 28px rgba(0,0,0,.25);
    overflow: hidden;
  }
  .brand {
    display: flex;
    align-items: center;
    gap: 10px;
  }
  .brand-dot {
    width: 16px; height: 16px;
    border-radius: 50%;
    background: var(--yellow);
  }
  .brand-name {
    color: var(--ink);
    font-weight: 700;
    font-size: 40px;
    line-height: 1;
    letter-spacing: .5px;
  }
  /* back side */
  .card-back .brand {
    position: absolute;
    right: 56px;
    top: 164px;
  }
  .card-back .brand-name { font-size: 34px; }
  .tagline {
    position: absolute;
    right: 58px;
    top: 212px;
    color: var(--ink);
    font-size: 15px;
  }
  /* front side */
  .card-front .brand {
    position: absolute;
    left: 36px;
    top: 140px;
  }
  .divider {
    position: absolute;
    left: 282px;
    top: 70px;
    width: 1px;
    height: 180px;
    background: linear-gradient(to bottom, transparent, var(--rule) 30%, var(--rule) 70%, transparent);
  }
  .details {
    position: absolute;
    left: 302px;
    top: 92px;
    color: var(--ink);
    font-size: 15px;
    line-height: 1.4;
  }
  .person-name { color: var(--green); font-weight: 700; font-size: 15px; text-transform: uppercase; }
  .person-role { color: var(--yellow); font-weight: 700; font-size: 16px; text-transform: uppercase; }
  .location { margin-bottom: 10px; }
  .contact-list { list-style: none; }
  .contact-list li { display: flex; align-items: center; gap: 8px; }
  .icon { width: 12px; height: 12px; flex: none; }
</style>
</head>
<body>
  <section class="card card-back" aria-label="Card back">
    <div class="brand">
      <span class="brand-dot"></span>
      <span class="brand-name">Kelvoria</span>
    </div>
    <p class="tagline">Hacemos más por ti!</p>
  </section>

  <section class="card card-front" aria-label="Card front">
    <div class="brand">
      <span class="brand-dot"></span>
      <span class="brand-name">Kelvoria</span>
    </div>
    <div class="divider"></div>
    <div class="details">
      <p class="person-name">Tomas Bilbrea</p>
      <p class="person-role">Managing Director</p>
      <p class="location">Melbourne, Australia</p>
      <ul class="contact-list">
        <li>
          <svg class="icon" viewBox="0 0 12 12"><circle cx="6" cy="6" r="6" fill="#8fdc8a"/><path d="M3.5 3.2h1.4l.6 1.5-.8.6a4 4 0 0 0 2 2l.6-.8 1.5.6v1.4c-3 .2-5.5-2.3-5.3-5.3z" fill="#0f5a6b"/></svg>
          <span>+61 491058264</span>
        </li>
        <li>
          <svg class="icon" viewBox="0 0 12 12"><circle cx="6" cy="6" r="6" fill="#8fdc8a"/><rect x="3" y="4" width="6" height="4.2" fill="none" stroke="#0f5a6b" stroke-width="1"/><path d="M3 4l3 2.3L9 4" fill="none" stroke="#0f5a6b" stroke-width="1"/></svg>
          <span>tomas@kelvarin.com.au</span>
        </li>
        <li>
          <svg class="icon" viewBox="0 0 12 12"><circle cx="6" cy="6" r="6" fill="#8fdc8a"/><circle cx="6" cy="6" r="3" fill="none" stroke="#0f5a6b" stroke-width="1"/><path d="M3 6h6M6 3c-1.5 2-1.5 4 0 6M6 3c1.5 2 1.5 4 0 6" fill="none" stroke="#0f5a6b" stroke-width=".8"/></svg>
          <span>www.kelvoria.com.au</span>
        </li>
      </ul>
    </div>
  </section>
</body>
</html>
```